*** Business Card Design Project

As a starting point, please take a look at our website www.plurvanta.com as a starting point.

We are looking for you to design our new business cards for plurvanta, something funky, cool and potentially unusual/different.

Good luck.

Industry/Entity Type

Business

```html
<!DOCTYPE html>
<html lang="en">
<head>
<meta charset="utf-8">
<title>Plurvanta – Business Cards</title>
<link rel="stylesheet" href="https://fonts.googleapis.com/css2?family=Fira+Sans+Condensed:wght@500;600&family=Josefin+Sans:wght@400;600&display=swap">
<style>
  :root {
    --backdrop: #e9ecee;
    --card: #ffffff;
    --ink: #2b2b2b;
    --ink-soft: #3a3a3a;
    --orange: #ef7f1a;
    --orange-fade: rgba(239, 127, 26, 0);
    --on-orange: #ffffff;
  }
  * { margin: 0; padding: 0; box-sizing: border-box; }
  html, body {
    width: 1200px; height: 960px; overflow: hidden;
    background: var(--backdrop);
  }
  .sheet {
    position: relative; width: 1200px; height: 960px;
  }
  .card {
    position: absolute; left: 290px;
    width: 620px; height: 370px;
    background: var(--card);
    box-shadow: 0 6px 24px rgba(0,0,0,0.12);
    overflow: hidden;
  }
  .card--front { top: 85px; }
  .card--back { top: 505px; }

  .wordmark {
    font-family: "Fira Sans Condensed", "Arial Narrow", sans-serif;
    font-weight: 600; color: var(--ink);
    letter-spacing: -0.5px; line-height: 1;
  }
  .tagline {
    font-family: "Fira Sans Condensed", "Arial Narrow", sans-serif;
    font-weight: 500; color: var(--ink); letter-spacing: 0.5px;
  }

  /* Front */
  .card--front .wordmark {
    position: absolute; left: 120px; top: 118px; font-size: 74px;
  }
  .card--front .tagline {
    position: absolute; left: 124px; top: 204px; font-size: 27px;
  }
  .card--front .sweep {
    position: absolute; left: 0; top: 0; width: 620px; height: 370px;
  }

  /* Back */
  .card--back .wordmark {
    position: absolute; left: 34px; top: 44px; font-size: 38px;
  }
  .card--back .tagline {
    position: absolute; left: 36px; top: 86px; font-size: 15px;
  }
  .nameplate {
    position: absolute; right: 0; top: 40px;
    width: 300px; height: 74px;
    background: var(--orange); color: var(--on-orange);
    font-family: "Josefin Sans", sans-serif;
    padding: 14px 0 0 30px;
  }
  .nameplate__name { font-size: 22px; letter-spacing: 0.8px; }
  .nameplate__role { font-size: 17px; margin-top: 8px; letter-spacing: 0.5px; }
  .contact {
    position: absolute; left: 340px; top: 138px;
    font-family: "Josefin Sans", sans-serif;
    font-size: 15px; line-height: 18px; color: var(--ink-soft);
    list-style: none;
  }
  .address {
    position: absolute; left: 340px; top: 224px;
    font-family: "Josefin Sans", sans-serif; font-style: normal;
    font-size: 15px; line-height: 19px; color: var(--ink-soft);
  }
</style>
</head>
<body>
<main class="sheet">
  <section class="card card--front" aria-label="Card front">
    <svg class="sweep" viewBox="0 0 620 370" aria-hidden="true">
      <defs>
        <linearGradient id="sweepFade" x1="0" y1="0" x2="1" y2="0">
          <stop offset="0" stop-color="var(--orange)" stop-opacity="1"/>
          <stop offset="0.55" stop-color="#ef7f1a" stop-opacity="0.95"/>
          <stop offset="1" stop-color="#ef7f1a" stop-opacity="0"/>
        </linearGradient>
      </defs>
      <polygon points="0,264 620,208 620,214 0,272" fill="url(#sweepFade)"/>
    </svg>
    <div class="wordmark">Plurvanta</div>
    <div class="tagline">Executive Search</div>
  </section>

  <section class="card card--back" aria-label="Card back">
    <div class="wordmark">Plurvanta</div>
    <div class="tagline">Executive Search</div>
    <div class="nameplate">
      <div class="nameplate__name">Martin Ellery</div>
      <div class="nameplate__role">Managing Director</div>
    </div>
    <ul class="contact">
      <li>Tel: (+44) 0203 555 0142</li>
      <li>Mob: (+44) 07700 900417</li>
      <li>Email: martin@plurvanta.com</li>
      <li>Skype: martinplurvanta</li>
    </ul>
    <address class="address">14 - 16 Larkfield Row<br>London EC2M 4TZ</address>
  </section>
</main>
</body>
</html>
```